Landing Page for a new, High Production, farming technology

Brightfield Crate
We need a single landing page, with an email signup for more information.
We build self-contained, farming boxes out of ISO containers. These containers use hydroponics and LED lighting to provide a year round growing environment for crops. So, you could grow crops anywhere at any time of the year in any environment.
For the purpose of this site, we will be doing split testing between several different themes using different sites and keywords.
This site's focus should be providing our product to people searching for high production farming technology.
We'll be focusing on the following key words: Agriculture, aquaponics, farm, garden, hydroponics, organic food, subsistence farming, urban farming, vertical garden.
Target Market(s)
We are going to be using this page to judge that
Number of Pages Required
1 page
Look and feel
Each slider illustrates characteristics of the customer's brand and the style your logo design should communicate.

```html
<!DOCTYPE html>
<html lang="en">
<head>
<meta charset="utf-8">
<title>Brightfield Crate</title>
<link href="https://fonts.googleapis.com/css2?family=Poppins:wght@400;500;600;700&display=swap" rel="stylesheet">
<style>
:root{
  --header-bg:#f0f0f0;
  --ink:#2b2b2b;
  --orange:#e29a5a;
  --green:#7aa86a;
  --green-band:rgba(122,170,110,.82);
  --white:#ffffff;
  --footer-bg:#f7f7f7;
}
*{margin:0;padding:0;box-sizing:border-box}
html,body{width:1200px;height:1136px;overflow:hidden;font-family:'Poppins',sans-serif;color:var(--ink)}
.page{position:relative;width:1200px;height:1136px;background:var(--footer-bg)}
.site-header{position:absolute;top:0;left:0;width:1200px;height:90px;background:var(--header-bg)}
.brand{position:absolute;left:90px;top:28px;display:flex;align-items:center;gap:10px}
.brand-mark{width:28px;height:28px;background:var(--orange)}
.brand-name{font-size:20px;font-weight:600;color:var(--green);letter-spacing:.5px}
.main-nav{position:absolute;left:432px;top:32px;display:flex;gap:27px;font-size:18px;font-weight:500}
.main-nav a{color:var(--ink);text-decoration:none}
.header-signup{position:absolute;left:1025px;top:27px;width:100px;height:35px;border:2px solid var(--orange);border-radius:18px;color:var(--orange);font-weight:600;font-size:16px;display:flex;align-items:center;justify-content:center}
.hero-photo{position:absolute;top:90px;left:0;width:1200px;height:920px;background:linear-gradient(180deg,#8aa6d8 0%,#e8d2b8 22%,#6f9a3e 40%,#4f7a2c 70%,#5b7d4a 100%)}
.hero-title{position:absolute;top:412px;left:0;width:1200px;text-align:center;font-size:48px;font-weight:700;color:var(--white)}
.signup-frame{position:absolute;left:272px;top:494px;width:657px;height:63px;border:2px solid var(--white)}
.signup-input{position:absolute;left:9px;top:9px;width:518px;height:41px;background:var(--white);border-radius:2px;font-size:12px;color:#333;padding-left:16px;line-height:41px}
.signup-button{position:absolute;left:540px;top:9px;width:103px;height:41px;background:var(--orange);color:var(--white);font-weight:600;font-size:16px;display:flex;align-items:center;justify-content:center}
.slider-arrow{position:absolute;top:400px;width:32px;height:32px;border-radius:50%;background:#1a1a1a}
.slider-arrow.prev{left:97px}.slider-arrow.next{left:1070px}
.slider-arrow svg{position:absolute;left:0;top:0}
.welcome-band{position:absolute;left:0;top:650px}
.welcome{position:absolute;top:725px;left:0;width:1200px;text-align:center;color:var(--white)}
.welcome h1{font-size:41px;font-weight:700;line-height:62px}
.welcome p{width:840px;margin:10px auto 0;font-size:14px;line-height:24px}
.read-more{display:inline-block;margin-top:24px;width:131px;height:37px;border:2px solid var(--white);border-radius:19px;font-size:16px;font-weight:600;line-height:33px}
.site-footer{position:absolute;top:1010px;left:0;width:1200px;height:126px;text-align:center}
.social{display:flex;justify-content:center;gap:3px;margin-top:34px}
.social span{width:27px;height:27px;border:1px solid var(--ink);border-radius:50%}
.copyright{margin-top:14px;font-size:13px}
</style>
</head>
<body>
<div class="page">
  <header class="site-header">
    <div class="brand"><span class="brand-mark"></span><span class="brand-name">Brightfield Crate</span></div>
    <nav class="main-nav"><a>Home</a><a>About</a><a>Products</a><a>Why Brightfield Crate?</a><a>Contact</a></nav>
    <div class="header-signup">SIGN UP</div>
  </header>

  <div class="hero-photo" role="img" aria-label="Greenhouse interior with long rows of leafy green crops under bright grow lights"></div>

  <div class="slider-arrow prev"><svg width="32" height="32"><path d="M18 10l-6 6 6 6" stroke="#fff" stroke-width="2.5" fill="none"/></svg></div>
  <div class="slider-arrow next"><svg width="32" height="32"><path d="M14 10l6 6-6 6" stroke="#fff" stroke-width="2.5" fill="none"/></svg></div>

  <div class="hero-title">Brightfield Crate</div>
  <div class="signup-frame">
    <div class="signup-input">Enter your email</div>
    <div class="signup-button">SIGNUP</div>
  </div>

  <svg class="welcome-band" width="1200" height="360" viewBox="0 0 1200 360">
    <path d="M0 75 Q600 -60 1200 75 L1200 360 L0 360 Z" fill="var(--green-band)"/>
    <path d="M42 79 Q600 -50 1158 79" stroke="#fff" stroke-width="2" fill="none"/>
  </svg>

  <section class="welcome">
    <h1>welcome to brightfield crate</h1>
    <p>Sed ut perspiciatis unde omnis iste natus error sit voluptatem accusantium doloremque laudantium, totam rem aperiam, eaque ipsa quae ab illo inventore veritatis et quasi architecto beatae vitae dicta sunt explicabo. Nemo enim ipsam voluptatem quia voluptas sit aspernatur aut odit aut fugit, sed quia consequuntur magni dolores eos qui ratione voluptatem sequi nesciunt. Neque porro quisquam est, qui dolorem ipsum quia dolor sit amet, consectetur, adipisci velit</p>
    <div class="read-more">Read More</div>
  </section>

  <footer class="site-footer">
    <div class="social"><span></span><span></span><span></span><span></span></div>
    <p class="copyright">© Copyright 2018 Brightfield Crate. All Rights Reserved.</p>
  </footer>
</div>
</body>
</html>
```